Brightfen Business Card Redesign & Logo Update

We need to update our business cards to something more modern and fresh. Brightfen can provide the current color schemes and old design examples, but welcome creativity in helping us with this redesign. PLEASE NOTE that we no longer utilize the "tree" and/or "leaf" imagery in our branding. If able would apprecaite an update on the quality of our "words only" logo in Ai. / PNG formats too.

Target Market(s)

Investors, landowners, corporate partners, contractors

Industry/Entity Type

Environmental Restoration & Conservation

Contact Information for Business Card

Logo, persons name, title, mailing address, phone and email, website url

Font styles to use
Other font styles liked:
• Merriweather

Requirements
Nice to have
• Logo, persons name, title, mailing address, phone and email, website url, but open to ideams
Should not have
• No all back backgrounds

```html
<!DOCTYPE html>
<html lang="en">
<head>
<meta charset="utf-8">
<title>Brightfen Business Cards</title>
<link rel="stylesheet" href="https://fonts.googleapis.com/css2?family=Oswald:wght@500;700&family=Open+Sans:wght@400;700&display=swap">
<style>
  :root {
    --stage: #3a3a3d;
    --card: #f5f2ea;
    --ink: #26282b;
    --orange: #ee7f22;
    --green: #138140;
    --white: #ffffff;
    --font-display: "Oswald", "Arial Narrow", sans-serif;
    --font-body: "Open Sans", Arial, sans-serif;
  }
  * { box-sizing: border-box; margin: 0; padding: 0; }
  html, body { width: 1200px; height: 780px; overflow: hidden; }
  body { background: var(--stage); position: relative; }

  .card {
    position: absolute;
    width: 620px;
    height: 340px;
    background: var(--card);
    border-radius: 20px;
    overflow: hidden;
    box-shadow: 0 10px 24px rgba(0,0,0,.4);
  }
  .card--front { left: 60px; top: 40px; }
  .card--back { left: 520px; top: 410px; }

  .logo { position: absolute; text-align: center; line-height: 1; }
  .logo__name {
    display: block;
    font-family: var(--font-display);
    font-weight: 700;
    color: var(--green);
    text-transform: uppercase;
    letter-spacing: 1px;
  }
  .logo__tagline {
    display: block;
    font-family: var(--font-display);
    font-weight: 500;
    color: var(--ink);
    text-transform: uppercase;
    letter-spacing: -0.3px;
  }

  .card--front .logo { left: 0; right: 0; top: 82px; }
  .card--front .logo__name { font-size: 118px; }
  .card--front .logo__tagline { font-size: 33px; margin-top: 6px; }

  .card--back .logo { right: 36px; top: 30px; }
  .card--back .logo__name { font-size: 62px; }
  .card--back .logo__tagline { font-size: 17.5px; margin-top: 3px; }

  .contact {
    position: absolute;
    left: 340px;
    top: 140px;
    list-style: none;
    font-family: var(--font-body);
    font-size: 16px;
    color: var(--ink);
  }
  .contact__item { display: flex; align-items: center; gap: 10px; height: 27px; white-space: nowrap; }
  .contact__icon { width: 16px; height: 16px; flex: none; }

  .bands { position: absolute; inset: 0; }

  .person {
    position: absolute;
    left: 30px;
    top: 268px;
    color: var(--white);
    font-family: var(--font-body);
    line-height: 1.15;
  }
  .person__name { font-size: 26px; font-weight: 700; }
  .person__title { font-size: 17px; font-weight: 400; }
</style>
</head>
<body>

  <section class="card card--front" aria-label="Business card front">
    <div class="logo">
      <span class="logo__name">Brightfen</span>
      <span class="logo__tagline">Environmental Credit Company</span>
    </div>
  </section>

  <section class="card card--back" aria-label="Business card back">
    <svg class="bands" viewBox="0 0 620 340" width="620" height="340" aria-hidden="true">
      <polygon fill="var(--green)" points="360,296 620,296 620,340 420,340"/>
      <path fill="var(--orange)" d="M0,250 H285 Q300,250 312,256 L430,340 H0 Z"/>
    </svg>

    <div class="logo">
      <span class="logo__name">Brightfen</span>
      <span class="logo__tagline">Environmental Credit Company</span>
    </div>

    <ul class="contact">
      <li class="contact__item">
        <svg class="contact__icon" viewBox="0 0 16 16" aria-hidden="true">
          <path fill="var(--orange)" d="M3.2 1.2l2.3 2.6-1.3 1.7c.9 2 2.4 3.5 4.3 4.4l1.7-1.3 2.6 2.3-1.4 2.3C6.4 13 3 9.6 1 4.6z"/>
        </svg>
        <span>(555) 014-2760</span>
      </li>
      <li class="contact__item">
        <svg class="contact__icon" viewBox="0 0 16 16" aria-hidden="true">
          <rect x="1" y="3" width="14" height="10" rx="1" fill="var(--orange)"/>
          <path d="M1.5 3.8L8 9l6.5-5.2" fill="none" stroke="var(--card)" stroke-width="1.3"/>
        </svg>
        <span>info@brightfen.com</span>
      </li>
      <li class="contact__item">
        <svg class="contact__icon" viewBox="0 0 16 16" aria-hidden="true">
          <circle cx="8" cy="8" r="7" fill="var(--orange)"/>
          <path d="M1 8h14M8 1c-3 3-3 11 0 14M8 1c3 3 3 11 0 14" fill="none" stroke="var(--card)" stroke-width="1"/>
        </svg>
        <span>www.brightfen.com</span>
      </li>
      <li class="contact__item">
        <svg class="contact__icon" viewBox="0 0 16 16" aria-hidden="true">
          <path fill="var(--orange)" d="M8 1a5 5 0 0 0-5 5c0 3.6 5 9 5 9s5-5.4 5-9a5 5 0 0 0-5-5z"/>
          <circle cx="8" cy="6" r="1.8" fill="var(--card)"/>
        </svg>
        <span>48 Reed Ln, Fairview, TX</span>
      </li>
    </ul>

    <div class="person">
      <p class="person__name">Elena Marsh</p>
      <p class="person__title">Co-Founder</p>
    </div>
  </section>

</body>
</html>
```